Website design for Silver Harbor Trading Inc

We are looking to build a website for our company. We are a scrap metal recycling company based out of Los Angeles. We purchase scrap metal in the US and ship them to China for recycling into fresh metal ores to supply industrial users. We would designs that emphasize the color green given our name and the nature of our business. Recycling themes are welcomed. We already have a URL at:
http://silverharbortradinginc.example/
At this point, I would like 4 pages:
- Home page
- About Us
- Resources
- Contact us
Our sister company is Maple Crest Intl Inc and they have a website that we can use as a starting point.
http://www.maplecrest-intl.example/
Our competitor has a website below. However we dislike the design given we believe it looks rather dull.
http://www.orientalloysalvage.example/en/
Lastly, this is for a website shell only. Please design the template, graphics, and color schemes. We will write the contents later.

```html
<!DOCTYPE html>
<html lang="en">
<head>
<meta charset="utf-8">
<title>Silver Harbor Trading</title>
<link href="https://fonts.googleapis.com/css2?family=PT+Sans:wght@400;700&family=Signika:wght@400;600&display=swap" rel="stylesheet">
<style>
:root{
  --header-dark:#1b1b1b;
  --header-mid:#333;
  --orange:#ee7d0c;
  --orange-light:#f59a1e;
  --orange-dark:#d9660a;
  --logo-green:#a6c63b;
  --heading-orange:#e06a10;
  --text:#4d4d4d;
  --text-soft:#6e6e6e;
  --panel:#efefef;
  --line:#dcdcdc;
  --label-green:#7a8e1e;
  --white:#fff;
}
*{box-sizing:border-box;margin:0;padding:0}
html,body{width:1118px;height:1200px;overflow:hidden}
body{font-family:"PT Sans",sans-serif;color:var(--text);background:var(--white);position:relative}
.wrap{position:absolute;left:84px;width:952px}

.site-header{position:absolute;top:0;left:0;width:1118px;height:128px;
  background:radial-gradient(ellipse at 70% 40%,#4a4a4a 0%,var(--header-mid) 30%,var(--header-dark) 80%)}
.brand{top:22px;display:flex;align-items:center;gap:12px}
.brand-mark{width:70px;height:70px;border-radius:50%;background:var(--orange)}
.brand-name{font-family:"Signika",sans-serif;font-weight:400;font-size:39px;line-height:39px;color:var(--logo-green)}
.social{position:absolute;right:82px;top:28px;display:flex;gap:14px}
.social span{width:28px;height:28px;background:linear-gradient(#fafafa,#cfcfcf);border-radius:2px}
.call{position:absolute;right:82px;top:70px;color:#ddd;font-size:23px;display:flex;align-items:center;gap:8px}
.call strong{color:var(--white);font-weight:700;font-size:26px}

.main-nav{position:absolute;top:128px;left:0;width:1118px;height:50px;
  background:linear-gradient(var(--orange-light),var(--orange))}
.main-nav ul{list-style:none;display:flex;position:absolute;left:84px;top:0;height:50px;border-left:1px solid var(--orange-dark)}
.main-nav li{height:50px;padding:0 20px;line-height:50px;color:var(--white);font-weight:700;font-size:16px;border-right:1px solid var(--orange-dark);text-shadow:0 1px 1px rgba(0,0,0,.3)}
.main-nav li.active{background:var(--orange-dark)}
.search{position:absolute;right:82px;top:9px;width:263px;height:32px;background:var(--white);border-radius:2px;font-size:14px;color:#777;padding:7px 13px}
.search i{position:absolute;right:5px;top:5px;width:23px;height:22px;background:linear-gradient(#bbb,#888);border-radius:2px;display:flex;align-items:center;justify-content:center}

.hero-band{position:absolute;top:178px;left:0;width:1118px;height:371px;background:var(--panel);border-bottom:1px solid var(--line)}
.slide{top:12px;height:336px;background:var(--white);padding:4px;box-shadow:0 12px 14px -10px rgba(0,0,0,.45)}
.slide-photo{position:relative;width:100%;height:100%;background:linear-gradient(160deg,#6d7c8c 0%,#4e5d6d 55%,#3b4756 100%)}
.slide-photo::after{content:"";position:absolute;left:300px;top:20px;width:440px;height:300px;border-radius:40%;background:radial-gradient(ellipse,#b23a2e 0%,rgba(178,58,46,.5) 45%,rgba(0,0,0,0) 70%)}
.slide-title{position:absolute;right:44px;top:28px;text-align:right;color:var(--white);font-weight:700;font-size:26px;line-height:32px;text-shadow:0 2px 3px rgba(0,0,0,.6);z-index:1}
.arrow{position:absolute;top:146px;width:34px;height:34px;border-radius:50%;background:rgba(255,255,255,.85);display:flex;align-items:center;justify-content:center;z-index:1}
.arrow.prev{left:27px}.arrow.next{right:27px}
.dots{position:absolute;top:345px;left:0;width:1118px;display:flex;justify-content:center;gap:9px}
.dots span{width:13px;height:13px;border-radius:50%;background:#aaa}
.dots span.on{background:#666}

.intro{top:571px;text-align:center}
.intro h1{font-size:26px;font-weight:700;color:#3c3c3c}
.intro p{font-size:17px;color:var(--text-soft);font-weight:700;margin-top:6px}
.rule{top:655px;height:1px;background:var(--line)}

.about{top:678px;width:680px;left:85px}
.section-title{font-size:24px;font-weight:700;color:var(--heading-orange);margin-bottom:12px}
.about p{font-size:14px;line-height:23.5px;color:var(--text)}
.about-photo{float:right;width:245px;height:130px;margin:0 0 4px 16px;border:3px solid #e2e2e2;
  background:linear-gradient(170deg,#8a929a 0%,#5b6269 50%,#3a3f45 100%)}
.about p+p{margin-top:7px}

.services{top:678px;left:790px;width:251px}
.services ul{list-style:none}
.services li{height:38px;margin-bottom:4.5px;background:linear-gradient(#fbfbfb,#ececec);border:1px solid #e0e0e0;display:flex;align-items:center;gap:10px;padding-left:12px;font-size:17px;font-weight:700;color:#777}

.contact-box{top:965px;height:131px;border:1px solid var(--line);display:flex;background:linear-gradient(#fff,#f6f6f6)}
.contact-info{width:465px;border-right:1px solid var(--line);display:flex;padding:10px 16px;font-size:14px;line-height:20px}
.contact-info h3,.quote h3{font-size:16px;font-weight:400;color:var(--label-green);margin-bottom:14px}
.col-addr{width:129px}.col-phone{width:103px}
.quote{padding:10px 18px;flex:1}
.quote-form{display:grid;grid-template-columns:191px 191px 60px;gap:13px 10px}
.field{height:32px;border:1px solid #d5d5d5;background:var(--white);font-size:14px;color:#555;padding:7px 13px;box-shadow:inset 0 -2px 2px rgba(0,0,0,.04)}
.submit{grid-column:3;grid-row:2;height:32px;background:linear-gradient(#a8a8a8,#7d7d7d);color:var(--white);font-weight:700;font-size:13px;border-radius:2px;display:flex;align-items:center;justify-content:center}

.site-footer{position:absolute;top:1111px;left:0;width:1118px;height:89px;background:var(--panel);border-top:1px solid var(--line);text-align:center;font-size:14px;color:#555}
.site-footer nav{margin-top:21px}
.site-footer nav span{margin:0 8px}
.site-footer p{margin-top:14px}
</style>
</head>
<body>
<header class="site-header">
  <div class="wrap brand">
    <div class="brand-mark"></div>
    <div class="brand-name">Silver Harbor<br>Trading</div>
  </div>
  <div class="social"><span></span><span></span><span></span></div>
  <div class="call">
    <svg width="24" height="20" viewBox="0 0 24 20"><path d="M4 2c2-1 3 0 4 2l1 3c0 1-1 2-2 2 1 3 3 5 6 6 0-1 1-2 2-2l3 1c2 1 3 2 2 4-1 2-3 2-5 1C9 17 5 13 3 7 2 5 2 3 4 2z" fill="#aaa"/></svg>
    Call us : <strong>555 210 4830</strong>
  </div>
</header>

<nav class="main-nav">
  <ul>
    <li class="active">HOME</li><li>ABOUT US</li><li>RESOURCES</li><li>CONTACT US</li>
  </ul>
  <div class="search">Search
    <i><svg width="14" height="14" viewBox="0 0 14 14"><circle cx="6" cy="6" r="4" stroke="#fff" stroke-width="2" fill="none"/><path d="M9 9l4 4" stroke="#fff" stroke-width="2"/></svg></i>
  </div>
</nav>

<section class="hero-band">
  <div class="wrap slide">
    <div class="slide-photo" role="img" aria-label="Container ship loaded with cargo sailing across open sea">
      <div class="slide-title">MORBI ULTRICIES<br>METUS EUISMOD PLACERAT</div>
      <div class="arrow prev"><svg width="12" height="14" viewBox="0 0 12 14"><path d="M8 2L3 7l5 5" stroke="#999" stroke-width="1.5" fill="none"/></svg></div>
      <div class="arrow next"><svg width="12" height="14" viewBox="0 0 12 14"><path d="M4 2l5 5-5 5" stroke="#999" stroke-width="1.5" fill="none"/></svg></div>
    </div>
  </div>
  <div class="dots"><span class="on"></span><span></span><span></span><span></span></div>
</section>

<section class="wrap intro">
  <h1>We are a scrap metal recycling company based out of Los Angeles.</h1>
  <p>We purchase scrap metal in the US and ship them to China for recycling into fresh metal ores to supply industrial users</p>
</section>
<div class="wrap rule"></div>

<section class="wrap about">
  <h2 class="section-title">About Silver Harbor Trading</h2>
  <p><span class="about-photo" role="img" aria-label="Large pile of shredded scrap metal in a yard"></span>Donec consequat tincidunt nisl, eu tincidunt mauris imperdiet at. Nam scelerisque rhoncus leo, a bibendum ipsum placerat a. Curabitur massa tortor, faucibus quis dui eu, consectetur vehicula diam. Aliquam hendrerit ligula non tortor blandit, at convallis nunc fermentum. Inte ger sodales tristique tincidunt. Phasellus sed sapien sed urna aliquet consequat. Viva mus lacinia lacus sapien, at semper.</p>
  <p>Nam eget eros blandit, accumsan tortor quis, scelerisque odio. Aenean laoreet, justo vel blandit auctor, tortor arcu condimentum lacus, vel venenatis libero ante eu justo. Morbi ultricies, metus id euismod placerat, turpis lorem convallis lacus, vel laoreet ipsum sapien at eros.</p>
</section>

<aside class="wrap services">
  <h2 class="section-title">Our Services</h2>
  <ul>
    <li><svg width="12" height="10" viewBox="0 0 12 10"><path d="M0 0l5 5-5 5zM6 0l5 5-5 5z" fill="#777"/></svg>Maecenas ultricies enim</li>
    <li><svg width="12" height="10" viewBox="0 0 12 10"><path d="M0 0l5 5-5 5zM6 0l5 5-5 5z" fill="#777"/></svg>Curabitur iaculis</li>
    <li><svg width="12" height="10" viewBox="0 0 12 10"><path d="M0 0l5 5-5 5zM6 0l5 5-5 5z" fill="#777"/></svg>Aliquam hendrerit ligula</li>
    <li><svg width="12" height="10" viewBox="0 0 12 10"><path d="M0 0l5 5-5 5zM6 0l5 5-5 5z" fill="#777"/></svg>Phasellus sed</li>
    <li><svg width="12" height="10" viewBox="0 0 12 10"><path d="M0 0l5 5-5 5zM6 0l5 5-5 5z" fill="#777"/></svg>Praesent ultrices nulla</li>
  </ul>
</aside>

<section class="wrap contact-box">
  <div class="contact-info">
    <div class="col-addr"><h3>Address :</h3>55 Building name<br>Street name,<br>City - Zip code</div>
    <div class="col-phone"><h3>Phone :</h3>555 210 4830<br>555 210 4830</div>
    <div class="col-email"><h3>Email :</h3>support@silverharbortradinginc.example</div>
  </div>
  <div class="quote">
    <h3>Get a Quote</h3>
    <div class="quote-form">
      <div class="field">Name</div><div class="field">Email</div><div></div>
      <div class="field">Phone</div><div class="field">Message</div>
      <div class="submit">SUBMIT</div>
    </div>
  </div>
</section>

<footer class="site-footer">
  <nav>Home<span>|</span>About us<span>|</span>Resources<span>|</span>Contact us</nav>
  <p>Copyright © 2013 &nbsp; Silver Harbor Trading. &nbsp;All rights reserved.</p>
</footer>
</body>
</html>
```